Business Card Design

Online clothing womens clothing store, I sell my clothing online and at the markets.

i would like the attached picture on the front of the card and the contact information on the back.

Industry/Entity Type

Business

Contact Information for Business Card

Marlow Thread
Karen Whitfield
(Instagram symbol) _marlow_thread_
(Facebook symbol) www.fakebookexample.com/marlowthreadau/

W : www.marlowthread.example.au
E : info@marlowthread.example.au
P : 0498716204

```html
<!DOCTYPE html>
<html lang="en">
<head>
<meta charset="utf-8">
<title>Marlow Thread — Business Card</title>
<link rel="stylesheet" href="https://fonts.googleapis.com/css2?family=Jost:wght@300&family=Arimo:wght@400&display=swap">
<style>
  :root {
    --page: #ececec;
    --ink: #111111;
    --paper: #ffffff;
    --card-black: #000000;
    --band: rgba(38, 36, 34, 0.82);
    --photo-warm-top: #ddd6cb;
    --photo-warm-bottom: #b8ae9b;
    --photo-field-top: #e9e9e7;
    --photo-field-bottom: #c8ccb6;
    --photo-front-top: #e2e0da;
    --photo-front-mid: #a9a496;
    --photo-front-bottom: #7d7b5e;
  }
  html, body {
    margin: 0;
    padding: 0;
    width: 1189px;
    height: 1200px;
    overflow: hidden;
    background: var(--page);
  }
  .card {
    position: absolute;
    left: 140px;
    width: 918px;
    height: 523px;
    overflow: hidden;
  }
  .card--contact { top: 46px; background: var(--paper); }
  .card--cover { top: 623px; }
  .card__art {
    position: absolute;
    inset: 0;
    width: 100%;
    height: 100%;
  }
  .brand {
    position: absolute;
    left: 0;
    right: 0;
    text-align: center;
    font-family: "Jost", sans-serif;
    font-weight: 300;
    text-transform: uppercase;
    white-space: nowrap;
  }
  .card--contact .brand {
    top: 100px;
    font-size: 54px;
    letter-spacing: 9px;
    color: var(--ink);
    padding-left: 10px;
  }
  .card--cover .brand {
    top: 232px;
    font-size: 64px;
    letter-spacing: 11px;
    color: var(--paper);
  }
  .holder {
    position: absolute;
    left: 108px;
    top: 380px;
    font-family: "Arimo", sans-serif;
    font-size: 30px;
    letter-spacing: 4px;
    color: var(--paper);
    white-space: nowrap;
  }
  .divider {
    position: absolute;
    left: 459px;
    top: 317px;
    width: 2px;
    height: 182px;
    background: var(--paper);
  }
  .contact-list {
    position: absolute;
    left: 510px;
    top: 316px;
    margin: 0;
    padding: 0;
    list-style: none;
    font-family: "Arimo", sans-serif;
    font-size: 21.5px;
    color: var(--paper);
  }
  .contact-list li {
    display: flex;
    align-items: center;
    height: 38.5px;
    white-space: nowrap;
  }
  .contact-icon {
    width: 16px;
    height: 16px;
    margin-right: 12px;
    flex: none;
  }
</style>
</head>
<body>

<section class="card card--contact" aria-label="Card back with contact details">
  <svg class="card__art" viewBox="0 0 918 523" aria-hidden="false">
    <defs>
      <linearGradient id="warmPhoto" x1="0" y1="0" x2="0" y2="1">
        <stop offset="0" stop-color="var(--photo-warm-top)"/>
        <stop offset="1" stop-color="var(--photo-warm-bottom)"/>
      </linearGradient>
      <linearGradient id="fieldPhoto" x1="0" y1="0" x2="0" y2="1">
        <stop offset="0" stop-color="var(--photo-field-top)"/>
        <stop offset="1" stop-color="var(--photo-field-bottom)"/>
      </linearGradient>
    </defs>
    <rect x="0" y="0" width="463" height="290" fill="url(#warmPhoto)" role="img" aria-label="Faded photo of two women sitting on a wooden porch step"/>
    <rect x="463" y="0" width="455" height="290" fill="url(#fieldPhoto)" role="img" aria-label="Faded photo of a woman in a long dress walking through a grassy field"/>
    <path d="M0,170 Q459,440 918,170 L918,523 L0,523 Z" fill="var(--card-black)"/>
    <path d="M40,186 Q459,424 885,176" fill="none" stroke="var(--paper)" stroke-width="5"/>
  </svg>

  <div class="brand">Marlow Thread</div>

  <div class="holder">Karen Whitfield</div>
  <div class="divider"></div>

  <ul class="contact-list">
    <li>
      <svg class="contact-icon" viewBox="0 0 16 16" aria-hidden="true">
        <rect width="16" height="16" rx="2" fill="#fff"/>
        <path d="M5 3.5 L6.8 3.5 L7.4 6 L6.2 7 Q7.2 9.2 9 10 L10 8.8 L12.5 9.4 L12.5 11.2 Q7.5 12 4.6 6.2 Z" fill="#000"/>
      </svg>
      0498716204
    </li>
    <li>
      <svg class="contact-icon" viewBox="0 0 16 16" aria-hidden="true">
        <rect x="1" y="3.5" width="14" height="9.5" fill="#fff"/>
        <path d="M1.5 4 L8 9 L14.5 4" fill="none" stroke="#000" stroke-width="1.3"/>
      </svg>
      info@marlowthread.example.au
    </li>
    <li>
      <svg class="contact-icon" viewBox="0 0 16 16" aria-hidden="true">
        <rect width="16" height="16" rx="2" fill="#fff"/>
        <circle cx="8" cy="8" r="5" fill="none" stroke="#000" stroke-width="1.3"/>
        <path d="M3 8 H13 M8 3 Q5 8 8 13 M8 3 Q11 8 8 13" fill="none" stroke="#000" stroke-width="1"/>
      </svg>
      www.marlowthread.example.au
    </li>
    <li>
      <svg class="contact-icon" viewBox="0 0 16 16" aria-hidden="true">
        <rect width="16" height="16" rx="2" fill="#fff"/>
      </svg>
      marlowthreadau
    </li>
    <li>
      <svg class="contact-icon" viewBox="0 0 16 16" aria-hidden="true">
        <rect width="16" height="16" rx="2" fill="#fff"/>
      </svg>
      marlow_thread
    </li>
  </ul>
</section>

<section class="card card--cover" aria-label="Card front with brand name over photo">
  <svg class="card__art" viewBox="0 0 918 523">
    <defs>
      <linearGradient id="frontPhoto" x1="0" y1="0" x2="0" y2="1">
        <stop offset="0" stop-color="var(--photo-front-top)"/>
        <stop offset="0.55" stop-color="var(--photo-front-mid)"/>
        <stop offset="1" stop-color="var(--photo-front-bottom)"/>
      </linearGradient>
    </defs>
    <rect x="0" y="0" width="918" height="523" fill="url(#frontPhoto)" role="img" aria-label="Photo of two women in boots sitting on a wooden porch beside open steps, hills in the background"/>
    <rect x="0" y="217" width="918" height="118" fill="var(--band)"/>
  </svg>
  <div class="brand">Marlow Thread</div>
</section>

</body>
</html>
```